Business card design needed

I run a Beautician studio (for 7 years now)
I offer
- Velmo Body Sugaring
- Ruby Glaze
- Nails
- Facials
- Manicure
- Foot Treatment
It might not be necessary to list all those treatments?
Maybe the link to the Website is sufficient?
I leave that up to you ...
(more info on www.FernAndDewByLenka.com.au)
Velmo BodySugaring is our biggest success, It replaces waxing.
I would like to incorporate the logo into the Business Card.
We had many complaints regarding our old Business Cards as the Phone Number was to small.
On the backside, we would like a "your next Appointment" section.
Looking forward to you Design, cheers ... Lenka
Industry/Entity Type
Business
Contact Information for Business Card
Fern by Dew by Lenka
14 Korrin Sqr 3942 Berwick
www.FernAndDewByLenka.com.au
03 9481 2267

```html
<!DOCTYPE html>
<html lang="en">
<head>
<meta charset="utf-8">
<title>Fern by Dew by Lenka – Business Cards</title>
<link rel="stylesheet" href="https://fonts.googleapis.com/css2?family=Cinzel:wght@400;500&family=Marcellus&family=Open+Sans:wght@400;600;700&family=Arimo:wght@400&display=swap">
<style>
  :root {
    --backdrop: #1c1c1c;
    --card: #ffffff;
    --green: #1a9447;
    --ink: #222222;
    --grey: #555555;
    --rule: #666666;
    --sun-top: #f6b21a;
    --sun-bottom: #e7611f;
    --faint: #eceff0;
  }
  * { box-sizing: border-box; margin: 0; padding: 0; }
  html, body { width: 1200px; height: 719px; overflow: hidden; }
  body {
    background: var(--backdrop);
    font-family: "Open Sans", sans-serif;
    color: var(--ink);
    position: relative;
  }
  .card {
    position: absolute;
    width: 525px;
    height: 298px;
    background: var(--card);
    border-radius: 14px;
    overflow: hidden;
  }
  .card--front { left: 50px; top: 40px; }
  .card--hours { left: 52px; top: 372px; }
  .card--appt-a { left: 606px; top: 40px; }
  .card--appt-b { left: 615px; top: 375px; }

  .center { position: absolute; left: 0; width: 100%; text-align: center; }

  /* Brand mark stand-in */
  .brand-dot {
    position: absolute;
    border-radius: 50%;
    background: linear-gradient(var(--sun-top), var(--sun-bottom));
  }
  .brand-name {
    position: absolute;
    left: 0; width: 100%;
    text-align: center;
    font-family: "Cinzel", serif;
    font-weight: 400;
    color: var(--ink);
    letter-spacing: 2px;
  }

  .front-dot { left: 227px; top: 24px; width: 70px; height: 70px; }
  .front-name { top: 104px; font-size: 20px; }
  .front-title { top: 160px; font-family: "Arimo", sans-serif; font-size: 24px; color: var(--green); letter-spacing: 1px; }
  .front-address { top: 195px; font-family: "Arimo", sans-serif; font-size: 16px; letter-spacing: 1.2px; }
  .front-contact { top: 228px; display: flex; justify-content: center; align-items: center; gap: 16px; font-family: "Arimo", sans-serif; }
  .front-contact .phone { font-size: 16px; display: flex; align-items: center; gap: 6px; }
  .front-contact .web { font-size: 14px; display: flex; align-items: center; gap: 6px; }
  .front-treat-title { top: 254px; font-size: 15px; font-weight: 700; letter-spacing: 1px; }
  .front-treat-list { top: 275px; font-size: 12.5px; }

  .hours-dot { left: 215px; top: 20px; width: 95px; height: 95px; }
  .hours-name { top: 128px; font-size: 26px; }
  .hours-web { top: 202px; font-size: 14px; letter-spacing: 2.6px; }
  .hours-title { top: 232px; font-size: 20px; font-weight: 700; color: var(--grey); letter-spacing: 1px; }
  .hours-times { top: 267px; font-size: 15px; font-weight: 600; color: var(--grey); }
  .hours-times .sep { color: #aaa; margin: 0 8px; font-weight: 400; }

  /* Appointment card */
  .appt > * { position: absolute; }
  .appt-title { left: 35px; top: 52px; font-family: "Marcellus", serif; font-size: 18px; color: var(--green); letter-spacing: 0.5px; }
  .appt-label { font-size: 14.5px; color: #333; }
  .dotline { height: 0; border-bottom: 1px dotted #444; }
  .solidline { height: 0; border-bottom: 1px solid #666; }
  .box { width: 95px; height: 20px; border: 1px solid #555; }
  .day { font-size: 14.5px; font-weight: 600; color: var(--grey); }
  .daybox { width: 33px; height: 20px; border: 1px solid #555; }
  .appt-note { left: 31px; top: 248px; width: 470px; font-size: 12.8px; line-height: 18px; color: #333; }
  .appt-faint-dot { left: 190px; top: 20px; width: 140px; height: 140px; border-radius: 50%; background: var(--faint); opacity: 0.6; }
  .appt-faint-name { left: 0; width: 100%; top: 262px; text-align: center; font-family: "Cinzel", serif; font-size: 22px; color: var(--faint); letter-spacing: 3px; }
  .appt-mark-dot { left: 407px; top: 22px; width: 42px; height: 42px; border-radius: 50%; background: linear-gradient(var(--sun-top), var(--sun-bottom)); }
  .appt-mark-name { left: 360px; width: 136px; top: 70px; text-align: center; font-family: "Cinzel", serif; font-size: 11px; color: var(--ink); letter-spacing: 1px; }
</style>
</head>
<body>

<!-- Front -->
<section class="card card--front">
  <div class="brand-dot front-dot"></div>
  <div class="brand-name front-name">Velmo Body Sugaring</div>
  <div class="center front-title">Fern by Dew by Lenka</div>
  <div class="center front-address">14 Korrin Sqr 3942 Berwick</div>
  <div class="center front-contact">
    <span class="phone">
      <svg width="15" height="15" viewBox="0 0 16 16" aria-hidden="true"><circle cx="8" cy="8" r="7.5" fill="#f0a020"/><path d="M5 4.5l1.6-.4 1 2-1 .8a6 6 0 0 0 2.5 2.5l.8-1 2 1-.4 1.6c-3.6.3-6.8-2.9-6.5-6.5z" fill="#fff"/></svg>
      03 9481 2267
    </span>
    <span class="web">
      <svg width="15" height="15" viewBox="0 0 16 16" aria-hidden="true"><circle cx="8" cy="8" r="6.5" fill="none" stroke="#f0a020" stroke-width="1.4"/><ellipse cx="8" cy="8" rx="2.8" ry="6.5" fill="none" stroke="#f0a020" stroke-width="1.1"/><path d="M1.5 8h13M3 4.5h10M3 11.5h10" stroke="#f0a020" stroke-width="1"/></svg>
      www.FernAndDewByLenka.com.au
    </span>
  </div>
  <div class="center front-treat-title">Treatments offer</div>
  <div class="center front-treat-list">• Velmo Body Sugaring &nbsp;• Ruby Glaze &nbsp;• Nails &nbsp;• Facials &nbsp;• Manicure &nbsp;• Foot Treatment</div>
</section>

<!-- Hours -->
<section class="card card--hours">
  <div class="brand-dot hours-dot"></div>
  <div class="brand-name hours-name">Velmo Body Sugaring</div>
  <div class="center hours-web">www.FernAndDewByLenka.com.au</div>
  <div class="center hours-title">Hours of Operation</div>
  <div class="center hours-times">Mon - Fri: 7.30am - 7.00pm<span class="sep">|</span>Saturday: 7.30am - 12.00pm</div>
</section>

<!-- Appointment, version A -->
<section class="card card--appt-a appt">
  <div class="appt-faint-dot"></div>
  <div class="appt-faint-name">Velmo Body Sugaring</div>
  <div class="appt-title">YOUR APPOINTMENT</div>
  <div class="appt-label" style="left:35px;top:89px">Name :</div>
  <div class="dotline" style="left:94px;top:103px;width:290px"></div>
  <div class="appt-label" style="left:35px;top:127px">Date :</div>
  <div class="solidline" style="left:94px;top:140px;width:95px"></div>
  <div class="appt-label" style="left:194px;top:127px">Time :</div>
  <div class="solidline" style="left:239px;top:140px;width:90px"></div>
  <div class="appt-label" style="left:331px;top:127px">am / pm</div>
  <div class="appt-label" style="left:35px;top:164px">Next Appointment</div>
  <div class="box" style="left:175px;top:163px"></div>
  <div class="box" style="left:301px;top:163px"></div>
  <div class="day" style="left:31px;top:201px">MON</div><div class="daybox" style="left:76px;top:202px"></div>
  <div class="day" style="left:115px;top:201px">TUE</div><div class="daybox" style="left:152px;top:202px"></div>
  <div class="day" style="left:191px;top:201px">WED</div><div class="daybox" style="left:234px;top:202px"></div>
  <div class="day" style="left:273px;top:201px">THU</div><div class="daybox" style="left:312px;top:202px"></div>
  <div class="day" style="left:351px;top:201px">FRI</div><div class="daybox" style="left:382px;top:202px"></div>
  <div class="day" style="left:421px;top:201px">SAT</div><div class="daybox" style="left:456px;top:202px"></div>
  <p class="appt-note">It would be appreciated if 24 hours notice could be given if you are unable to attend an appointment</p>
</section>

<!-- Appointment, version B -->
<section class="card card--appt-b appt">
  <div class="appt-mark-dot"></div>
  <div class="appt-mark-name">Velmo Body Sugaring</div>
  <div class="appt-title">YOUR APPOINTMENT</div>
  <div class="appt-label" style="left:35px;top:89px">Name :</div>
  <div class="dotline" style="left:94px;top:103px;width:290px"></div>
  <div class="appt-label" style="left:35px;top:127px">Date :</div>
  <div class="solidline" style="left:94px;top:140px;width:95px"></div>
  <div class="appt-label" style="left:194px;top:127px">Time :</div>
  <div class="solidline" style="left:239px;top:140px;width:90px"></div>
  <div class="appt-label" style="left:331px;top:127px">am / pm</div>
  <div class="appt-label" style="left:35px;top:164px">Next Appointment</div>
  <div class="box" style="left:175px;top:163px"></div>
  <div class="box" style="left:301px;top:163px"></div>
  <div class="day" style="left:31px;top:201px">MON</div><div class="daybox" style="left:76px;top:202px"></div>
  <div class="day" style="left:115px;top:201px">TUE</div><div class="daybox" style="left:152px;top:202px"></div>
  <div class="day" style="left:191px;top:201px">WED</div><div class="daybox" style="left:234px;top:202px"></div>
  <div class="day" style="left:273px;top:201px">THU</div><div class="daybox" style="left:312px;top:202px"></div>
  <div class="day" style="left:351px;top:201px">FRI</div><div class="daybox" style="left:382px;top:202px"></div>
  <div class="day" style="left:421px;top:201px">SAT</div><div class="daybox" style="left:456px;top:202px"></div>
  <p class="appt-note">It would be appreciated if 24 hours notice could be given if you are unable to attend an appointment</p>
</section>

</body>
</html>
```